Falkrin homes and renovations business card design.

Would like some new card designs utilizing my new logo that look professional. I am open to different colors on the logo or utilize the same ones we have. I like the original concept but would like to see some fresh ideas and build on what we have already done.

Target Market(s)

Custom home building industry, Real estate sales, Renovation projects.

Industry/Entity Type

Home Builder

Contact Information for Business Card

Falkrin Homes and Renovations
2871 96th Avenue
Corvane, Westmark
T2R3W8
Home : 403- 718-4063 Cell: 403- 294-5170

My info is : Dax Falkrin, President and CEO
email: falkrinhomes@maildrop-example.net
Website: falkrinhomes-example.com
websit

Requirements
Must have
• Must Use my new logo design. I am open to different colors on the logo or utilize the same ones in the existing design. I can upload the original logo design if needed.

```html
<!DOCTYPE html>
<html lang="en">
<head>
<meta charset="utf-8">
<title>Falkrin Homes and Renovations – Business Card</title>
<link href="https://fonts.googleapis.com/css2?family=Exo+2:wght@400;500;700&family=Montserrat:wght@600&display=swap" rel="stylesheet">
<style>
  :root {
    --stage: #2b2b2d;
    --card-dark: #161616;
    --map-tone-a: #262626;
    --map-tone-b: #1b1b1b;
    --card-light: #ffffff;
    --gold: #b5853a;
    --gold-bright: #f6bd22;
    --ink: #3a3a3c;
    --web-grey: #c9c9c9;
  }
  * { box-sizing: border-box; margin: 0; padding: 0; }
  html, body { width: 1200px; height: 1000px; overflow: hidden; }
  body {
    background: var(--stage);
    font-family: "Exo 2", "Helvetica Neue", Arial, sans-serif;
    position: relative;
  }
  .card {
    position: absolute;
    left: 250px;
    width: 700px;
    height: 400px;
    overflow: hidden;
    box-shadow: 0 18px 40px rgba(0,0,0,.45);
  }

  /* brand lockup: one colour, one weight */
  .brand { display: flex; align-items: center; gap: 14px; }
  .brand-square { width: 14px; height: 14px; background: var(--gold); flex: none; }
  .brand-name {
    font-family: "Montserrat", Arial, sans-serif;
    font-weight: 600;
    color: var(--gold);
    text-transform: uppercase;
    line-height: 1;
  }
  .brand-name .brand-word { display: block; font-size: 44px; letter-spacing: 1px; }
  .brand-name .brand-line { display: block; font-size: 17px; letter-spacing: .5px; margin-top: 4px; }

  /* ---------- back side ---------- */
  .card--back { top: 70px; background: var(--card-dark); }
  .card--back .world-map {
    position: absolute;
    inset: 20px 30px 30px 30px;
    background: radial-gradient(ellipse at 50% 45%, var(--map-tone-a) 0%, var(--map-tone-b) 70%, transparent 100%);
    border-radius: 40%;
  }
  .back-brand {
    position: absolute;
    left: 0; right: 0; top: 150px;
    justify-content: center;
  }
  .back-web {
    position: absolute;
    left: 0; right: 0; top: 292px;
    display: flex; justify-content: center; align-items: center; gap: 10px;
    color: var(--web-grey);
    font-size: 17px;
    letter-spacing: 1px;
  }
  .back-web .highlight { color: var(--gold-bright); }

  /* ---------- front side ---------- */
  .card--front { top: 510px; background: var(--card-light); }
  .front-brand { position: absolute; left: 44px; top: 34px; }
  .front-brand .brand-word { font-size: 40px; }
  .front-brand .brand-line { font-size: 16px; }
  .name-block { position: absolute; left: 0; top: 130px; display: flex; align-items: flex-start; }
  .name-tab { width: 22px; height: 44px; background: var(--gold); border-radius: 0 8px 8px 0; margin-right: 22px; }
  .person-name { font-size: 28px; font-weight: 700; color: var(--ink); letter-spacing: 1.5px; line-height: 1; }
  .person-title { font-size: 16px; color: var(--gold); margin-top: 5px; }
  .address { position: absolute; left: 44px; top: 214px; color: var(--ink); font-size: 17px; line-height: 1.3; letter-spacing: 1px; font-style: normal; }
  .contact-list { position: absolute; left: 44px; top: 270px; list-style: none; color: var(--ink); font-size: 17px; letter-spacing: 1px; }
  .contact-list li { display: flex; align-items: center; gap: 12px; height: 22px; }
  .contact-list svg { width: 14px; height: 14px; flex: none; }
  .front-band { position: absolute; left: 0; bottom: 0; width: 700px; height: 56px; }
</style>
</head>
<body>

<section class="card card--back" aria-label="Business card back">
  <div class="world-map" role="img" aria-label="Faint world map background"></div>
  <div class="brand back-brand">
    <div class="brand-square"></div>
    <div class="brand-name"><span class="brand-word">Falkrin</span><span class="brand-line">Homes and Renovations</span></div>
  </div>
  <div class="back-web">
    <svg width="16" height="16" viewBox="0 0 16 16" aria-hidden="true">
      <circle cx="9" cy="7" r="5" fill="none" stroke="var(--gold-bright)" stroke-width="2"/>
      <line x1="5.5" y1="10.5" x2="1.5" y2="14.5" stroke="var(--gold-bright)" stroke-width="2.4" stroke-linecap="round"/>
    </svg>
    <span>www.<span class="highlight">falkrinhomes-example</span>.com</span>
  </div>
</section>

<section class="card card--front" aria-label="Business card front">
  <div class="brand front-brand">
    <div class="brand-square"></div>
    <div class="brand-name"><span class="brand-word">Falkrin</span><span class="brand-line">Homes and Renovations</span></div>
  </div>

  <div class="name-block">
    <div class="name-tab"></div>
    <div>
      <div class="person-name">DAX FALKRIN</div>
      <div class="person-title">President and CEO</div>
    </div>
  </div>

  <address class="address">
    2871 96th Avenue<br>Corvane, Westmark
  </address>

  <ul class="contact-list">
    <li>
      <svg viewBox="0 0 14 14" aria-hidden="true"><path d="M3 1 L5 1 L6 4 L4.5 5.5 Q6 8.5 8.5 9.5 L10 8 L13 9 L13 11 Q12 13 10 13 Q2 11 1 3 Q1 1 3 1Z" fill="var(--gold)"/></svg>
      403 718 4063
    </li>
    <li>
      <svg viewBox="0 0 14 14" aria-hidden="true"><rect x="3.5" y="1" width="7" height="12" rx="1.2" fill="none" stroke="var(--gold)" stroke-width="1.4"/><circle cx="7" cy="11" r=".8" fill="var(--gold)"/></svg>
      403 294 5170
    </li>
    <li>
      <svg viewBox="0 0 14 14" aria-hidden="true"><rect x="1" y="3" width="12" height="8.5" fill="var(--gold)"/><path d="M1 3 L7 8 L13 3" fill="none" stroke="#fff" stroke-width="1"/></svg>
      falkrinhomes@maildrop-example.net
    </li>
  </ul>

  <svg class="front-band" viewBox="0 0 700 56" aria-hidden="true">
    <polygon points="0,0 545,26 530,56 0,56" fill="var(--gold)"/>
    <polygon points="558,27 700,33 700,56 543,56" fill="var(--gold-bright)"/>
  </svg>
</section>

</body>
</html>
```